Tech Startup needs Cool Business Card Designs

Looking for help Polishing our Business Card designs. We are a startup in the Knowledge management space that is releasing a product called TideNook which is a personal and group Digital Library. We're looking for help making our card designs standout. We already have a bunch of files to work from. Just need someone with an experienced eye to put everything together.

Target Market(s)

Knowledge Workers: people who work with alot of digital information on a daily basis and have problems keeping track and organizing everything. Special business cases; Researchers, Teacher/Trainers, Project Managers, Group Organizers, Nonprofit community managers, business owners, etc

Industry/Entity Type

Business

Contact Information for Business Card

Two Sided;
1) Backside is a digital library. I included several examples in the attached files. The digital library MUST use all of the ICONS attached. The digital library must look modern and sleek building off the concepts on the two attached files "BACK_'
2) Front- just needs to use the color scheme and style of the back into a modern hip yet professional design

Requirements
Must have
• - Designs for two sides
• - Back must be a representation of a digital library using ALL of the ICONS provided
• - Front must include all the main fields from Front business card design (but no QR code)
• - Must use TideNook Logo on both Front & Back
Should not have
• Do NOT NEED AREA FOR QR CODE

```html
<!DOCTYPE html>
<html lang="en">
<head>
<meta charset="utf-8">
<title>TideNook Business Card – Front and Back</title>
<link rel="stylesheet" href="https://fonts.googleapis.com/css2?family=Exo+2:wght@400;500;700&display=swap">
<style>
  :root {
    --page-bg: #e9ebee;
    --card-white: #ffffff;
    --brand-blue: #3a7fc0;
    --brand-orange: #f0582c;
    --library-light: #eaf2fa;
    --library-mid: #c9dcef;
    --ink-white: #ffffff;
    --card-shadow: rgba(20, 40, 70, 0.18);
  }
  * { margin: 0; padding: 0; box-sizing: border-box; }
  html, body {
    width: 1200px; height: 899px; overflow: hidden;
    background: var(--page-bg);
    font-family: "Exo 2", sans-serif;
  }
  .card {
    position: absolute; left: 250px;
    width: 700px; height: 400px;
    background: var(--card-white);
    border-radius: 36px;
    overflow: hidden;
    box-shadow: 0 12px 34px var(--card-shadow);
  }
  .card-front { top: 36px; }
  .card-back { top: 464px; }

  .card-shapes { position: absolute; left: 0; top: 0; }

  .brand {
    position: absolute;
    display: flex; align-items: center; gap: 12px;
  }
  .brand-dot {
    width: 36px; height: 36px; border-radius: 50%;
    background: var(--brand-orange); flex: none;
  }
  .brand-name {
    font-weight: 700; font-size: 45px; letter-spacing: -0.4px;
    color: var(--brand-blue); line-height: 1;
  }
  .card-front .brand { left: 45px; top: 117px; }
  .card-back .brand { left: 0; right: 0; top: 46px; justify-content: center; }

  .details {
    position: absolute; left: 436px; top: 48px;
    color: var(--ink-white);
  }
  .person-name {
    font-weight: 500; font-size: 19.5px; letter-spacing: 1.2px;
    text-transform: uppercase; line-height: 1.1;
  }
  .person-role { font-size: 15px; margin-top: 3px; }
  .address { font-size: 17px; line-height: 1.3; margin-top: 54px; }
  .contact-list { list-style: none; margin-top: 56px; }
  .contact-list li {
    display: flex; align-items: center; gap: 10px;
    font-size: 12.5px; letter-spacing: 0.6px; height: 22.5px;
  }
  .contact-list svg { width: 12.5px; height: 12.5px; flex: none; }

  .library-area {
    position: absolute; left: 70px; top: 130px;
    width: 560px; height: 230px;
    border-radius: 18px;
    background: linear-gradient(180deg, var(--library-light), var(--library-mid));
  }
</style>
</head>
<body>
  <div class="card card-front">
    <svg class="card-shapes" viewBox="0 0 900 514" width="700" height="400" preserveAspectRatio="none" aria-hidden="true">
      <path fill="var(--brand-blue)" d="M480 0 C600 80 620 300 120 514 L900 514 L900 0 Z"/>
      <path fill="var(--brand-orange)" d="M452 0 C585 90 592 312 34 514 L120 514 C620 300 600 80 480 0 Z"/>
    </svg>

    <div class="brand">
      <span class="brand-dot"></span>
      <span class="brand-name">TideNook</span>
    </div>

    <div class="details">
      <p class="person-name">Marcus Halley</p>
      <p class="person-role">Managing Director</p>
      <p class="address">214 9th floor, Harbor<br>Lane Road QTP</p>
      <ul class="contact-list">
        <li>
          <svg viewBox="0 0 16 16"><path fill="#fff" d="M3 1h3l1 4-2 1a9 9 0 0 0 5 5l1-2 4 1v3a2 2 0 0 1-2 2A13 13 0 0 1 1 3a2 2 0 0 1 2-2z"/></svg>
          020 481 7735
        </li>
        <li>
          <svg viewBox="0 0 16 16"><rect x="4" y="1" width="8" height="14" rx="1.5" fill="none" stroke="#fff" stroke-width="1.6"/><circle cx="8" cy="12.5" r="0.9" fill="#fff"/></svg>
          020 481 7736
        </li>
        <li>
          <svg viewBox="0 0 16 16"><rect x="4" y="1" width="8" height="5" fill="#fff"/><rect x="1" y="6" width="14" height="7" rx="1.5" fill="#fff"/><rect x="4" y="11" width="8" height="4" fill="#fff"/></svg>
          020 481 7737
        </li>
        <li>
          <svg viewBox="0 0 16 16"><rect x="1" y="3" width="14" height="10" rx="1.5" fill="#fff"/><path d="M2 4l6 5 6-5" fill="none" stroke="var(--brand-blue)" stroke-width="1.4"/></svg>
          hello@tidenook.com
        </li>
        <li>
          <svg viewBox="0 0 16 16" fill="none" stroke="#fff" stroke-width="1.3"><circle cx="8" cy="8" r="6.5"/><ellipse cx="8" cy="8" rx="3" ry="6.5"/><path d="M1.5 8h13"/></svg>
          www.tidenookapp.com
        </li>
      </ul>
    </div>
  </div>

  <div class="card card-back">
    <div class="brand">
      <span class="brand-dot"></span>
      <span class="brand-name">TideNook</span>
    </div>
    <div class="library-area" role="img" aria-label="Digital library illustration: shelves of documents, media and folders shown with the product icons"></div>
  </div>
</body>
</html>
```